Classy, Elegant, Simple Business Card Design

Looking to have a classy, simple, and elegant design. Want a top notch designed business card. I really like the look of the new torvane credit card. I also like the design I attached. I am trying to reach 21-29 year old females for booking us for there wedding or event. We offer Disc Jockey Service, Photo Booth Rentals, and Uplighting .

Target Market(s)

21-28 year old females

Contact Information for Business Card

Has to have logo, website, email, and phone number

Font styles to use
Other font styles liked:
• open to font choice, modern, clean
Designer to choose
33a6d7
0791cd
0555a3
ffffff

Requirements
Must have
• Has to have logo, website, email, and phone number
Nice to have
• I really like the design of the new torvane credit card. I also included my logo and some designs I like
Should not have
• clutter or too much info

```html
<!DOCTYPE html>
<html lang="en">
<head>
<meta charset="UTF-8">
<title>Tideline Event Group – Business Card</title>
<link href="https://fonts.googleapis.com/css2?family=Jost:wght@400;500;600&family=Poppins:wght@400&display=swap" rel="stylesheet">
<style>
  :root {
    --sky: #33a6d7;
    --azure: #0791cd;
    --royal: #0555a3;
    --navy: #0b2a55;
    --white: #ffffff;
    --grey: #8f8f8f;
    --ink: #333333;
    --backdrop: #e4e5e7;
  }
  * { box-sizing: border-box; margin: 0; padding: 0; }
  html, body {
    width: 1200px; height: 800px; overflow: hidden;
    background: var(--backdrop);
  }
  .sheet {
    width: 1200px; height: 800px;
    display: flex; align-items: center; justify-content: center; gap: 40px;
  }
  .card {
    width: 540px; height: 309px;
    background: var(--white);
    border-bottom: 4px solid var(--royal);
    border-left: 2px solid var(--azure);
    box-shadow: 0 10px 24px rgba(0,0,0,.18);
    position: relative;
  }

  /* Contact side */
  .card--contact .details {
    position: absolute; left: 150px; top: 104px;
    font-family: "Jost", sans-serif;
  }
  .person-name {
    font-size: 26px; font-weight: 400; letter-spacing: .5px;
    color: var(--navy); line-height: 1;
  }
  .person-name .surname { color: var(--azure); font-weight: 600; }
  .person-role {
    font-size: 13px; color: var(--grey); letter-spacing: .5px;
    margin: 4px 0 0 68px;
  }
  .contact-lines {
    margin-top: 12px;
    font-family: "Poppins", sans-serif;
    font-size: 12.5px; color: var(--ink); line-height: 1.6;
  }
  .contact-lines .web { margin-left: 80px; font-size: 11.5px; }

  /* Brand side */
  .brand {
    position: absolute; left: 0; right: 0; top: 92px;
    display: flex; align-items: center; justify-content: center; gap: 14px;
  }
  .brand-dot {
    width: 22px; height: 22px; border-radius: 50%;
    background: var(--azure);
  }
  .brand-name {
    font-family: "Jost", sans-serif;
    font-size: 34px; font-weight: 500; letter-spacing: 2px;
    color: var(--royal); line-height: 1; text-transform: uppercase;
  }
  .services {
    position: absolute; left: 0; right: 0; bottom: 58px;
    text-align: center;
    font-family: "Poppins", sans-serif;
    font-size: 14px; color: var(--ink); letter-spacing: .3px;
  }
  .services .sep { color: var(--azure); margin: 0 4px; }
</style>
</head>
<body>
  <main class="sheet">
    <section class="card card--contact" aria-label="Contact side">
      <div class="details">
        <h1 class="person-name">DANIEL <span class="surname">HARTLEY</span></h1>
        <p class="person-role">PRESIDENT</p>
        <p class="contact-lines">
          P-555-014-2870 E. info@tidelineevents.com<br>
          <span class="web">www.tidelineevents.com</span>
        </p>
      </div>
    </section>

    <section class="card card--brand" aria-label="Brand side">
      <div class="brand">
        <span class="brand-dot"></span>
        <span class="brand-name">Tideline Event Group</span>
      </div>
      <p class="services">
        Disc Jockey Service<span class="sep">•</span>Photo Booth Rentals<span class="sep">•</span>Uplighting .
      </p>
    </section>
  </main>
</body>
</html>
```